Pavecrest Works

Im looking for something similar to (tarvalepaving.com) web site. I really want it to pop!
services we offer:
- Seal Coating
- Crack Filling
- Striping
- Asphalt
- Concrete
- Signage
- Road Grinding
- Grading
- Hydro Blasting
- Recycled asphalt
- Dumpster Pads
- Pressure Washing
- Wheel blocks
- Bollard installation
- Commercial Curbing
- Job site clean up
- Sweeping
- Forestry Clean up
- ADA Compliant work
- Speed bump installation and removal
- Snow removal
- Custom stair sets (Commercial)
Target Market(s)
Parking lot maintenance, asphalt repairs, road grading
Industry/Entity Type
construction, parking lot maintenance
Number of Pages Required
2 page

```html
<!DOCTYPE html>
<html lang="en">
<head>
<meta charset="utf-8">
<title>Pavecrest Works — About Us</title>
<link href="https://fonts.googleapis.com/css2?family=Roboto:wght@400;500;700;900&display=swap" rel="stylesheet">
<style>
:root{
  --green:#5bea12;
  --black:#000;
  --ink:#333;
  --body:#555;
  --muted:#999;
  --field:#ececec;
  --white:#fff;
  --navy:#1e2a52;
}
*{box-sizing:border-box;margin:0;padding:0}
html,body{width:1200px;height:3712px;overflow:hidden}
body{position:relative;font-family:'Roboto',sans-serif;background:var(--white);color:var(--ink)}
.abs{position:absolute}
.btn{position:absolute;display:flex;align-items:center;justify-content:center;background:var(--green);color:var(--white);font-weight:500;border-radius:4px;box-shadow:0 4px 10px rgba(91,234,18,.3)}

/* header */
.site-header{left:0;top:0;width:1200px;height:89px;background:var(--black)}
.brand{position:absolute;left:75px;top:30px;color:var(--white);font-size:26px;font-weight:700;letter-spacing:.5px}
.nav a{position:absolute;top:37px;color:var(--white);font-size:14px;text-decoration:none}
.header-cta{position:absolute;left:981px;top:26px;width:143px;height:43px;border:1.5px solid var(--white);border-radius:3px;color:var(--white);font-size:15px;font-weight:500;display:flex;align-items:center;justify-content:center}

/* hero */
.hero{left:0;top:89px;width:1200px;height:602px;background:linear-gradient(180deg,#3a3c3b 0%,#2b2c2a 45%,#3d3b34 80%,#24231f 100%)}
.hero-title{left:0;top:232px;width:1200px;text-align:center;color:var(--white);font-size:66px;font-weight:700}
.hero-text{left:179px;top:337px;width:842px;text-align:center;color:var(--white);font-size:15px;line-height:26.3px}

/* headings */
.section-title{left:0;width:1200px;text-align:center;font-size:46px;font-weight:700;color:#333}

/* services */
.card{position:absolute;top:857px;width:311px;height:385px;background:var(--white);border-radius:4px;box-shadow:0 4px 18px rgba(0,0,0,.1);overflow:hidden}
.card-photo{width:311px;height:173px}
.card h3{margin-top:22px;text-align:center;font-size:19px;font-weight:500;color:#333}
.card p{margin:12px auto 0;width:270px;text-align:center;font-size:13px;line-height:26px;color:var(--body)}
.card .btn{left:88px;top:324px;width:135px;height:39px;font-size:14px}
.services-note{left:197px;top:1300px;width:806px;text-align:center;font-size:13px;line-height:26px;color:var(--body)}

/* why */
.why{left:0;top:1534px;width:1200px;height:758px;background:linear-gradient(180deg,#2a3232 0%,#1c2427 30%,#2a3038 60%,#262b30 100%)}
.why-text{left:208px;top:1679px;width:786px;text-align:center;color:var(--white);font-size:13px;line-height:26.5px}
.quote-form{left:213px;top:1806px;width:736px;height:385px;background:var(--white);border-radius:6px}
.field{position:absolute;background:var(--field);border-radius:4px;display:flex;align-items:center;padding-left:14px;color:#aaa;font-size:13px;gap:12px}
.field svg{width:18px;height:18px;flex:none}

/* gallery */
.tile{position:absolute;width:248px;height:308px}

/* testimonials */
.review{position:absolute;top:3312px;width:453px;height:305px;background:var(--white);box-shadow:0 4px 20px rgba(0,0,0,.1);border-radius:4px}
.avatar{position:absolute;left:34px;top:20px;width:60px;height:60px;border-radius:50%;color:var(--white);font-size:30px;font-weight:500;display:flex;align-items:center;justify-content:center}
.review .name{position:absolute;left:114px;top:40px;font-size:16px;font-weight:700;color:var(--navy)}
.stars{position:absolute;left:326px;top:38px;display:flex;gap:3px}
.review hr{position:absolute;left:32px;top:101px;width:389px;border:0;border-top:1px solid #e3e3e3}
.review p{position:absolute;left:32px;top:120px;width:392px;font-size:13px;line-height:27.5px;color:var(--body)}
.review .date{position:absolute;left:32px;top:257px;font-size:14px;color:var(--muted)}
.dot{position:absolute;top:3664px;width:10px;height:10px;border-radius:50%;background:#ddd}
</style>
</head>
<body>

<header class="abs site-header">
  <div class="brand">Pavecrest Works</div>
  <nav class="nav">
    <a style="left:606px">Home</a>
    <a style="left:677px">About Us</a>
    <a style="left:771px">Services</a>
    <a style="left:860px">Testimonials</a>
  </nav>
  <div class="header-cta">Get a Quote</div>
</header>

<section class="abs hero" role="img" aria-label="Dark photo of an underground parking garage with yellow striped pillars and a painted arrow"></section>
<h1 class="abs hero-title">ABOUT US</h1>
<p class="abs hero-text">Backed by 20 years experience, we understand the significance of every project we're assigned to no matter the size or complexity. Pavecrest Works stresses the importance of open dialogue with our clients so you know exactly what your project entails including cost, duration, and final results. Our high profile client reference list speaks for its self. Pavecrest Works takes great pride in exceeding all expectations.</p>
<div class="btn" style="left:497px;top:477px;width:206px;height:62px;font-size:20px">Get a Quote</div>

<h2 class="abs section-title" style="top:743px">Services</h2>

<article class="card" style="left:75px">
  <div class="card-photo" role="img" aria-label="Worker in orange painting white parking stripes" style="background:linear-gradient(135deg,#e8e8e6 0%,#d06a2a 45%,#4a4a48 75%,#e9d443 100%)"></div>
  <h3>Striping</h3>
  <p>Lorem ipsum dolor sit amet, consectetur adipisicing elit, sed do eiusmod tempor incididunt ut labore et dolore magna aliqua.</p>
  <div class="btn">Get a Quote</div>
</article>
<article class="card" style="left:444px">
  <div class="card-photo" role="img" aria-label="Worker pouring seal coat from a bucket onto asphalt" style="background:linear-gradient(160deg,#6d8a4a 0%,#4f5663 40%,#2a2b2d 75%,#3c3c3c 100%)"></div>
  <h3>Seal Coating</h3>
  <p>Lorem ipsum dolor sit amet, consectetur adipisicing elit, sed do eiusmod tempor incididunt ut labore et dolore magna aliqua.</p>
  <div class="btn">Get a Quote</div>
</article>
<article class="card" style="left:812px">
  <div class="card-photo" role="img" aria-label="Crack filling applicator on grey asphalt" style="background:linear-gradient(150deg,#2c2c2c 0%,#8f8f8d 40%,#b3b2ae 100%)"></div>
  <h3>Crack Filling</h3>
  <p>Lorem ipsum dolor sit amet, consectetur adipisicing elit, sed do eiusmod tempor incididunt ut labore et dolore magna aliqua.</p>
  <div class="btn">Get a Quote</div>
</article>

<p class="abs services-note">Lorem ipsum dolor sit amet, consectetur adipisicing elit, sed do eiusmod tempor incididunt ut labore et dolore magna aliqua. Ut enim ad minim veniam, quis nostrud exercitation ullamco laboris nisi ut aliquip ex ea commodo consequat. Duis aute irure dolor in reprehenderit in</p>
<div class="btn" style="left:500px;top:1391px;width:202px;height:58px;font-size:20px">View all Services</div>

<section class="abs why" role="img" aria-label="Dusk photo of a forest road with yellow centre lines"></section>
<h2 class="abs section-title" style="top:1591px;color:var(--white)">Why Choose Us?</h2>
<p class="abs why-text">It is our duty to our customers to provide honest, cost-effective solutions for your parking lot or driveway needs in the Orlando area and throughout Florida. Pavecrest Works is dependable and values every customer. We strive to keep an open and lasting relationship with every customer, even once the project is completed.</p>

<form class="abs quote-form">
  <div class="field" style="left:25px;top:25px;width:332px;height:49px">
    <svg viewBox="0 0 18 18" fill="none" stroke="#aaa" stroke-width="1.3"><circle cx="9" cy="6" r="3.5"/><path d="M2.5 17c0-4 3-6 6.5-6s6.5 2 6.5 6"/></svg>Your Name</div>
  <div class="field" style="left:379px;top:25px;width:334px;height:49px">
    <svg viewBox="0 0 18 18" fill="none" stroke="#aaa" stroke-width="1.3"><rect x="1.5" y="3.5" width="15" height="11" rx="1"/><path d="M1.5 4l7.5 6 7.5-6"/></svg>Your Email Address</div>
  <div class="field" style="left:25px;top:106px;width:332px;height:49px">
    <svg viewBox="0 0 18 18" fill="none" stroke="#aaa" stroke-width="1.3"><circle cx="9" cy="9" r="7.5"/><circle cx="9" cy="9" r="4"/></svg>Select Service
    <svg viewBox="0 0 18 18" fill="none" stroke="#999" stroke-width="1.4" style="position:absolute;right:14px;width:12px"><path d="M3 6l6 6 6-6"/></svg></div>
  <div class="field" style="left:379px;top:106px;width:334px;height:49px">
    <svg viewBox="0 0 18 18" fill="none" stroke="#aaa" stroke-width="1.3"><path d="M4 2l3 3-2 2c1 2 3 4 5 5l2-2 3 3-2 3C8 15 3 10 2 4z"/></svg>Enter Phone number</div>
  <div class="field" style="left:25px;top:182px;width:688px;height:88px;align-items:flex-start;padding-top:14px">
    <svg viewBox="0 0 18 18" fill="none" stroke="#aaa" stroke-width="1.3"><circle cx="9" cy="9" r="7.5"/><path d="M9 8v5M9 5v.5"/></svg>Any message for us?</div>
  <div class="btn" style="left:25px;top:299px;width:688px;height:59px;font-size:16px;border-radius:3px;box-shadow:none">GET A FREE QUOTE NOW</div>
</form>

<h2 class="abs section-title" style="top:2335px">Gallery</h2>
<div class="tile" style="left:76px;top:2448px;background:linear-gradient(180deg,#9bb0c0 0%,#6f8a5a 15%,#8a3b30 35%,#7a3129 100%)" role="img" aria-label="Red stamped brick-pattern asphalt crosswalk"></div>
<div class="tile" style="left:346px;top:2448px;background:linear-gradient(180deg,#b8cbe0 0%,#d1a521 45%,#373838 80%,#2b2b2b 100%)" role="img" aria-label="Yellow asphalt roller compactor"></div>
<div class="tile" style="left:612px;top:2448px;background:linear-gradient(180deg,#6b6b6b 0%,#8c8c88 40%,#b8b6ae 70%,#a39f95 100%)" role="img" aria-label="New concrete ramp with yellow tactile warning pad"></div>
<div class="tile" style="left:879px;top:2448px;background:linear-gradient(180deg,#c4ccd3 0%,#7d8a6c 12%,#8e3a30 30%,#7b332b 100%)" role="img" aria-label="Large red brick-pattern paved area"></div>
<div class="tile" style="left:76px;top:2772px;background:linear-gradient(180deg,#c8d9e6 0%,#2f4a2a 30%,#3b5a2c 65%,#6a6560 100%)" role="img" aria-label="Freshly paved road winding through pine trees"></div>
<div class="tile" style="left:346px;top:2772px;background:linear-gradient(135deg,#333 0%,#d4682a 45%,#dedede 70%,#e6cf3d 100%)" role="img" aria-label="Worker spraying white parking line paint"></div>
<div class="tile" style="left:612px;top:2772px;background:linear-gradient(180deg,#8a8460 0%,#6f6b55 40%,#dcbb2a 70%,#a9a8a2 100%)" role="img" aria-label="Yellow bollards in front of a utility building"></div>
<div class="tile" style="left:879px;top:2772px;background:linear-gradient(180deg,#8fa8bf 0%,#4d6b3e 30%,#3a3a3a 60%,#9f988b 100%)" role="img" aria-label="Compact track loader grading gravel"></div>

<h2 class="abs section-title" style="top:3144px">Testimonials</h2>
<p class="abs" style="left:0;top:3220px;width:1200px;text-align:center;font-size:13px;color:var(--body)">Don't take our word for it, see what our clients have to say about it</p>

<svg class="abs" style="left:75px;top:3455px" width="32" height="20" viewBox="0 0 32 20" fill="none" stroke="#1e2a52" stroke-width="2"><path d="M31 10H2M10 2L2 10l8 8"/></svg>
<svg class="abs" style="left:1093px;top:3455px" width="32" height="20" viewBox="0 0 32 20" fill="none" stroke="#1e2a52" stroke-width="2"><path d="M1 10h29M22 2l8 8-8 8"/></svg>

<article class="review" style="left:128px">
  <div class="avatar" style="background:#f47b7b">M</div>
  <div class="name">Maren Holt</div>
  <div class="stars">
    <svg width="15" height="15" viewBox="0 0 20 20"><path fill="#f5b400" d="M10 1l2.8 5.8 6.2.9-4.5 4.4 1 6.3L10 15.4 4.5 18.4l1-6.3L1 7.7l6.2-.9z"/></svg>
    <svg width="15" height="15" viewBox="0 0 20 20"><path fill="#f5b400" d="M10 1l2.8 5.8 6.2.9-4.5 4.4 1 6.3L10 15.4 4.5 18.4l1-6.3L1 7.7l6.2-.9z"/></svg>
    <svg width="15" height="15" viewBox="0 0 20 20"><path fill="#f5b400" d="M10 1l2.8 5.8 6.2.9-4.5 4.4 1 6.3L10 15.4 4.5 18.4l1-6.3L1 7.7l6.2-.9z"/></svg>
    <svg width="15" height="15" viewBox="0 0 20 20"><path fill="#f5b400" d="M10 1l2.8 5.8 6.2.9-4.5 4.4 1 6.3L10 15.4 4.5 18.4l1-6.3L1 7.7l6.2-.9z"/></svg>
    <svg width="15" height="15" viewBox="0 0 20 20"><path fill="#f5b400" d="M10 1l2.8 5.8 6.2.9-4.5 4.4 1 6.3L10 15.4 4.5 18.4l1-6.3L1 7.7l6.2-.9z"/></svg>
  </div>
  <hr>
  <p>Lorem ipsum dolor sit amet, consectetur adipisicing elit, sed do eiusmod tempor incididunt ut labore et dolore magna aliqua.<br>&nbsp;Ut enim ad minim veniam, quis nostrud exercitation ullamco laboris nisi ut aliquip ex ea commodo consequat.</p>
  <div class="date">August 13, 2021</div>
</article>

<article class="review" style="left:619px">
  <div class="avatar" style="background:#8fd3f5">T</div>
  <div class="name">Theo Lindqvist</div>
  <div class="stars">
    <svg width="15" height="15" viewBox="0 0 20 20"><path fill="#f5b400" d="M10 1l2.8 5.8 6.2.9-4.5 4.4 1 6.3L10 15.4 4.5 18.4l1-6.3L1 7.7l6.2-.9z"/></svg>
    <svg width="15" height="15" viewBox="0 0 20 20"><path fill="#f5b400" d="M10 1l2.8 5.8 6.2.9-4.5 4.4 1 6.3L10 15.4 4.5 18.4l1-6.3L1 7.7l6.2-.9z"/></svg>
    <svg width="15" height="15" viewBox="0 0 20 20"><path fill="#f5b400" d="M10 1l2.8 5.8 6.2.9-4.5 4.4 1 6.3L10 15.4 4.5 18.4l1-6.3L1 7.7l6.2-.9z"/></svg>
    <svg width="15" height="15" viewBox="0 0 20 20"><path fill="#f5b400" d="M10 1l2.8 5.8 6.2.9-4.5 4.4 1 6.3L10 15.4 4.5 18.4l1-6.3L1 7.7l6.2-.9z"/></svg>
    <svg width="15" height="15" viewBox="0 0 20 20"><path fill="#f5b400" d="M10 1l2.8 5.8 6.2.9-4.5 4.4 1 6.3L10 15.4 4.5 18.4l1-6.3L1 7.7l6.2-.9z"/></svg>
  </div>
  <hr>
  <p>Lorem ipsum dolor sit amet, consectetur adipisicing elit, sed do eiusmod tempor incididunt ut labore et dolore magna aliqua.<br>&nbsp;Ut enim ad minim veniam, quis nostrud exercitation ullamco laboris nisi ut aliquip ex ea commodo consequat.</p>
  <div class="date">August 13, 2021</div>
</article>

<span class="dot" style="left:554px;background:var(--green)"></span>
<span class="dot" style="left:580px"></span>
<span class="dot" style="left:607px"></span>
<span class="dot" style="left:632px"></span>

</body>
</html>
```